Fashion-Doll Website

I'm looking to create a new and better website for my growing fashion-doll brand, QUELLIE.

About me: I'm a Brooklyn-based artist, illustrator, and doll-maker and QUELLIE is the name of my doll. Quellie is a character doll (one girl) but she's not necessarily defined by any particular physical trait outside of the sculpt of the doll and her unique sense of style. For example, she could have pink hair and freckles or dark skin and green eyes, but she would still be "Quellie."

My partner and I created the current website ourselves using Adobe Muse. While it has served its purpose, we are not professional graphic or web designers, so I'm looking to graduate to a much more sophisticated and streamlined web design. I want the site to feel sweet and homespun but also hip and edgy. Because the site is so image heavy, I think black and white or black and off-white might be the best color palate, but I'm open to seeing other palates. Quellie's signature color is a muted lavender so maybe that could be integrated into the design. Here is the link:

www.QuellieDoll.example

I want the website to feel more like a shop and less like a gallery/info page. I'm now selling one-of-a-kind porcelain dolls, limited-edition resin dolls, face-plate necklaces, paper dolls, custom doll services, and printed Quellie throw pillows. I also need an interface that will allow me to create new categories, update inventory, and post new items easily.

I need to add new sections for press/articles, multiple image galleries (photography, products, illustrations, comics, and fan art), **collaboration projects, and several flash based doll "dress-up" games.

I would prefer a design that I can code/update myself using Adobe Muse. PSD files import into Muse, so I would prefer that you use them. I'm certainly not opposed to other designs, but I would prefer a design I can manage myself.

I'm including some photos and drawings of Quellie that express her look and vibe. I don't want to use these images in the web design necessarily (I think simple is best) but I thought they would be helpful in expressing the kind of girl she is and how I want the site to feel. I want to work with someone who has a clean, refined, yet whimsical aesthetic who can help me create a website that really expresses how special Quellie is.

Reason: I have had a family emergency come up and I can't devote time to this right now so I'm extending the deadline another 10 days.

Target Market(s)

young eccentrics, art collectors, fashion enthusiasts, and adult doll-collectors

Industry/Entity Type

Fashion

Requirements
Must have
• I need the following main categories: Info, Sales, Galleries, Press, and Dress-up. However, I don't necessarily want or expect the layout to be organized like the current website.

INFO:

*About Quellie (the character)

*Doll specifications: 27" porcelain doll, 22" porcelain doll, 22" resin doll, life-size doll (for window display)

*About the artist

SALES:

*Porcelain dolls

*Resin dolls

*Face-plate necklaces

*Pillows

*Custom doll/necklace info and inquiry form

GALLERIES:

*Photographs

*Collaboration projects

*Illustrations/Comics

*Fan Art/Contests

PRESS:

*An inventory of pdf's of articles about Quellie for users to download or view inside a reader online.

DRESS UP:

*Links to two interactive flash based dress-up games (interactive paper dolls)

Nice to have
• I hold online drawing and design contests from time to time so I would love to have a spot on the site reserved to host the rules and results of my contests.

Quellie has a large facebook and Instagram following so links to her social media would also be great.
instagram: @quelliedoll
facebook: fanpagehub.example/quelliedoll

Should not have
• I'm not looking to see anything too girly, too young, or too sexy.
Quellie is not Tessa, Marble Maiden, or Voxxi. She's a sophisticated young girl who is fresh, funky, and free-spirited.

```html
<!DOCTYPE html>
<html lang="en">
<head>
<meta charset="utf-8">
<title>QUELLIE — Handmade fashion dolls</title>
<link href="https://fonts.googleapis.com/css2?family=Tinos:wght@400;700&display=swap" rel="stylesheet">
<style>
  :root {
    --ink: #000000;
    --paper: #fdf4f4;
    --white: #ffffff;
    --lavender: #a79ad0;
    --price: #6b6a98;
    --muted: #4f4f4f;
    --nav: #d8d8d8;
    --small: #bfbfbf;
    --card-text: #111111;
    --social-a: #3b5a9a;
    --social-b: #7a5a48;
  }
  * { box-sizing: border-box; margin: 0; padding: 0; }
  html, body { width: 1200px; height: 1089px; overflow: hidden; background: var(--ink); }
  body { position: relative; font-family: "Tinos", "Times New Roman", serif; color: var(--nav); }
  a { color: var(--nav); text-decoration: none; }

  .brand { position: absolute; left: 369px; top: 30px; font-size: 27px; letter-spacing: 1px; color: var(--lavender); font-weight: 400; line-height: 1; }
  .brand-tm { position: absolute; left: 478px; top: 58px; font-size: 5px; color: var(--small); }

  .social-top { position: absolute; left: 807px; top: 21px; display: flex; gap: 7px; }
  .social-top span { display: block; width: 9px; height: 9px; background: var(--white); }

  .account-links { position: absolute; left: 720px; top: 51px; display: flex; gap: 10px; font-size: 7.5px; }

  .main-nav { position: absolute; left: 369px; top: 95px; display: flex; gap: 15px; font-size: 10px; letter-spacing: .4px; text-transform: uppercase; }

  .hero { position: absolute; left: 370px; top: 120px; width: 462px; height: 311px; border: 1px solid var(--small); }
  .hero-visual { position: absolute; left: 6px; top: 6px; width: 448px; height: 297px;
    background: linear-gradient(180deg, #8fb2d8 0%, #a7b4c2 35%, #8a8378 65%, #4c4641 100%); }
  .hero-title { position: absolute; left: 0; right: 0; top: 172px; text-align: center; font-size: 14px; font-weight: 700; letter-spacing: .6px; color: var(--white); }
  .hero-link { position: absolute; left: 0; right: 0; top: 192px; text-align: center; font-size: 6px; color: var(--white); }
  .hero-dots { position: absolute; left: 213px; top: 283px; display: flex; gap: 1px; }
  .hero-dots span { width: 7px; height: 7px; background: var(--white); opacity: .7; }
  .hero-dots span:first-child { opacity: 1; }

  .contests { position: absolute; left: 370px; width: 462px; top: 454px; text-align: center; }
  .contests h2 { font-size: 17px; font-weight: 400; color: var(--muted); letter-spacing: .3px; }
  .contests p { margin-top: 3px; font-size: 6px; color: var(--muted); }

  .shop-grid { position: absolute; left: 370px; top: 518px; display: grid; grid-template-columns: repeat(3, 148px); grid-auto-rows: 207px; column-gap: 8px; row-gap: 9px; }
  .product { position: relative; background: var(--paper); }
  .product-visual { position: absolute; left: 7px; top: 12px; width: 135px; height: 113px; }
  .product-name { position: absolute; left: 0; right: 0; top: 137px; text-align: center; font-size: 11.5px; font-weight: 400; line-height: 11.5px; color: var(--card-text); }
  .product-name.single { top: 142px; }
  .product-price { position: absolute; left: 0; right: 0; top: 172px; text-align: center; font-size: 11.5px; font-weight: 700; color: var(--price); }
  .product-more { position: absolute; left: 0; right: 0; top: 194px; text-align: center; font-size: 6px; font-weight: 700; color: var(--card-text); }

  .v-porcelain { background: linear-gradient(135deg, #cdbfa5, #6f7d57 55%, #3a3a2a); }
  .v-resin { background: linear-gradient(180deg, #b83a3a 0%, #e9e2db 40%, #d6ccc0 100%); }
  .v-necklace { background: linear-gradient(180deg, #e2539b 0%, #1b1b1b 35%, #111 100%); }
  .v-paper { background: linear-gradient(135deg, #ece9e2, #b9b2c4 50%, #e6ddd3); }
  .v-custom { background: linear-gradient(180deg, #e4ded6 0%, #4d5e3a 55%, #c45a46 100%); }
  .v-pillow { background: linear-gradient(135deg, #f2ece4, #c4b26a 45%, #4aa6c9 70%, #f0eae2); }

  .footer-nav { position: absolute; left: 369px; top: 978px; display: flex; gap: 7px; font-size: 8.5px; }
  .footer-nav a { color: var(--small); }
  .social-foot { position: absolute; left: 795px; top: 975px; display: flex; gap: 5px; }
  .social-foot span { display: block; width: 15px; height: 15px; }
  .social-foot .fb { background: var(--social-a); }
  .social-foot .ig { background: var(--social-b); }

  .footer-brand { position: absolute; left: 0; width: 1200px; top: 1040px; text-align: center; font-size: 19px; color: var(--lavender); letter-spacing: .8px; line-height: 1; }
  .footer-tagline { position: absolute; left: 0; width: 1200px; top: 1069px; text-align: center; font-size: 6px; color: var(--small); }
</style>
</head>
<body>
  <header>
    <div class="brand">QUELLIE</div>
    <div class="brand-tm">TM</div>
    <div class="social-top" aria-label="Social links">
      <span role="img" aria-label="Quellie on fanpagehub"></span>
      <span role="img" aria-label="@quelliedoll"></span>
    </div>
    <nav class="account-links">
      <a href="#">My Account</a><a href="#">Register</a><a href="#">Help</a><a href="#">Cart</a>
    </nav>
    <nav class="main-nav">
      <a href="#">Info</a><a href="#">Sales</a><a href="#">Galleries</a><a href="#">Press</a><a href="#">Dress-up</a>
    </nav>
  </header>

  <section class="hero">
    <div class="hero-visual" role="img" aria-label="Photograph of the featured Quellie doll in a dark dress with red roses, outdoors in front of city buildings"></div>
    <div class="hero-title">CLOUD WALKER QUELLIE</div>
    <div class="hero-link">- see details -</div>
    <div class="hero-dots"><span></span><span></span><span></span></div>
  </section>

  <section class="contests">
    <h2>DRAWING &amp; DESIGN CONTESTS</h2>
    <p>- check out -</p>
  </section>

  <main class="shop-grid">
    <article class="product">
      <div class="product-visual v-porcelain" role="img" aria-label="Photograph of a blonde porcelain doll with a black bow"></div>
      <h3 class="product-name">Name<br>Porcelain Quellie</h3>
      <div class="product-price">Price: $113</div>
      <a class="product-more" href="#">- See more -</a>
    </article>
    <article class="product">
      <div class="product-visual v-resin" role="img" aria-label="Illustration of a resin doll with red flowers in her hair"></div>
      <h3 class="product-name">Limited-edition<br>resin dolls</h3>
      <div class="product-price">Price: $113</div>
      <a class="product-more" href="#">- See more -</a>
    </article>
    <article class="product">
      <div class="product-visual v-necklace" role="img" aria-label="Photograph of a face-plate necklace worn on a black top"></div>
      <h3 class="product-name single">Face-plate necklaces</h3>
      <div class="product-price">Price: $113</div>
      <a class="product-more" href="#">- See more -</a>
    </article>
    <article class="product">
      <div class="product-visual v-paper" role="img" aria-label="Illustrated paper dolls with cut-out outfits"></div>
      <h3 class="product-name single">Paper dolls</h3>
      <div class="product-price">Price: $113</div>
      <a class="product-more" href="#">- See more -</a>
    </article>
    <article class="product">
      <div class="product-visual v-custom" role="img" aria-label="Photograph of three custom-styled dolls"></div>
      <h3 class="product-name">Custom<br>doll services</h3>
      <div class="product-price">Price: $113</div>
      <a class="product-more" href="#">- See more -</a>
    </article>
    <article class="product">
      <div class="product-visual v-pillow" role="img" aria-label="Illustration printed on a Quellie throw pillow"></div>
      <h3 class="product-name">Printed Quellie<br>throw pillows</h3>
      <div class="product-price">Price: $113</div>
      <a class="product-more" href="#">- See more -</a>
    </article>
  </main>

  <footer>
    <nav class="footer-nav">
      <a href="#">Info</a><a href="#">Sales</a><a href="#">Galleries</a><a href="#">Press</a><a href="#">Dress-up</a>
    </nav>
    <div class="social-foot">
      <span class="fb" role="img" aria-label="Quellie on fanpagehub"></span>
      <span class="ig" role="img" aria-label="@quelliedoll"></span>
    </div>
    <div class="footer-brand">QUELLIE</div>
    <div class="footer-tagline">Handmade in Larkfield, Eastborough.</div>
  </footer>
</body>
</html>
```